Thornvale Group needs a business card design

We need a new business card design using the logo recently selected in a logo competition on Pixel Bazaar. Our business is a consultancy specializing in aviation and energy and the winning business card design will promote an image of precision and professionalism with creativity.

Please use the logo with the name on the front of the card and use a complementary font. Make the back white with either the light grey or dark grey logo.

Target Market(s)

Senior finance and legal leaders at aviation and energy companies

Industry/Entity Type

Management Consulting

Contact Information for Business Card

Peter Castrell
President
Thornvale Group

www.thornvalegroup.example

(555) 204-6391
pc@thornvalegroup.example

Requirements
Must have
• Professional font that goes well with the logo font

```html
<!DOCTYPE html>
<html lang="en">
<head>
<meta charset="utf-8">
<title>Thornvale Group — Business Card</title>
<link href="https://fonts.googleapis.com/css2?family=Open+Sans:wght@400;700&family=Raleway:wght@300&display=swap" rel="stylesheet">
<style>
  :root {
    --page-bg: #e9e7e3;
    --navy-top: #3a8ab3;
    --navy-mid: #155a8a;
    --navy-bottom: #0a2c57;
    --ink-light: #ffffff;
    --ink-soft: rgba(255,255,255,0.82);
    --rule: rgba(255,255,255,0.55);
    --brand-blue: #2e6190;
    --card-white: #ffffff;
  }
  * { margin: 0; padding: 0; box-sizing: border-box; }
  html, body {
    width: 1200px; height: 913px; overflow: hidden;
    background: var(--page-bg);
  }
  .canvas {
    position: relative; width: 1200px; height: 913px;
  }
  .card {
    position: absolute; top: 306px;
    width: 525px; height: 300px;
    box-shadow: 0 10px 28px rgba(0,0,0,0.18);
  }
  .card--front {
    left: 50px;
    background: linear-gradient(160deg, var(--navy-top) 0%, var(--navy-mid) 45%, var(--navy-bottom) 100%);
    color: var(--ink-light);
  }
  .card--back {
    left: 625px;
    background: var(--card-white);
    display: flex; align-items: center; justify-content: center;
  }

  .brand {
    position: absolute; left: 40px; top: 0; bottom: 0; width: 205px;
    display: flex; flex-direction: column; justify-content: center; align-items: center;
    font-family: "Raleway", sans-serif; font-weight: 300;
    color: var(--ink-light); text-transform: uppercase; text-align: center;
  }
  .brand__mark {
    width: 14px; height: 14px; background: var(--ink-light); margin-bottom: 14px;
  }
  .brand__name { font-size: 27px; letter-spacing: 3px; line-height: 1; }
  .brand__sub { font-size: 12px; letter-spacing: 12px; margin-top: 10px; margin-right: -12px; }

  .divider {
    position: absolute; left: 262px; top: 62px; width: 1px; height: 176px;
    background: var(--rule);
  }

  .contact {
    position: absolute; left: 282px; top: 70px;
    font-family: "Open Sans", sans-serif;
  }
  .contact__name { font-size: 20px; font-weight: 700; line-height: 1.1; }
  .contact__title { font-size: 12px; color: var(--ink-soft); margin-top: 2px; }
  .contact__list { list-style: none; margin-top: 26px; }
  .contact__item {
    display: flex; align-items: center; gap: 8px;
    font-size: 12.5px; line-height: 20px; color: var(--ink-light);
  }
  .contact__icon { width: 10px; height: 10px; flex: none; }

  .back-brand {
    display: flex; align-items: center; gap: 14px;
    font-family: "Raleway", sans-serif; font-weight: 300;
    color: var(--brand-blue); font-size: 34px; letter-spacing: 3px; text-transform: uppercase;
  }
  .back-brand__mark { width: 18px; height: 18px; background: var(--brand-blue); }
</style>
</head>
<body>
<main class="canvas">
  <section class="card card--front" aria-label="Card front">
    <div class="brand">
      <span class="brand__mark"></span>
      <span class="brand__name">Thornvale</span>
      <span class="brand__sub">Group</span>
    </div>
    <div class="divider"></div>
    <div class="contact">
      <p class="contact__name">Peter Castrell</p>
      <p class="contact__title">President</p>
      <ul class="contact__list">
        <li class="contact__item">
          <svg class="contact__icon" viewBox="0 0 10 10"><path d="M2 0.5 L3.8 2.6 L2.9 3.6 Q4 6 6.4 7.1 L7.4 6.2 L9.5 8 L8.3 9.5 Q1 8 0.5 1.7 Z" fill="#fff"/></svg>
          (555) 204-6391
        </li>
        <li class="contact__item">
          <svg class="contact__icon" viewBox="0 0 10 10"><rect x="0.6" y="2" width="8.8" height="6.2" fill="none" stroke="#fff" stroke-width="1"/><path d="M0.8 2.3 L5 5.6 L9.2 2.3" fill="none" stroke="#fff" stroke-width="1"/></svg>
          pc@thornvalegroup.example
        </li>
        <li class="contact__item">
          <svg class="contact__icon" viewBox="0 0 10 10"><circle cx="5" cy="5" r="4.3" fill="none" stroke="#fff" stroke-width="1"/><ellipse cx="5" cy="5" rx="1.9" ry="4.3" fill="none" stroke="#fff" stroke-width="0.8"/><path d="M0.7 5 H9.3" stroke="#fff" stroke-width="0.8"/></svg>
          www.thornvalegroup.example
        </li>
      </ul>
    </div>
  </section>

  <section class="card card--back" aria-label="Card back">
    <div class="back-brand">
      <span class="back-brand__mark"></span>
      <span>Thornvale Group</span>
    </div>
  </section>
</main>
</body>
</html>
```